Bespoke Branding Agency "Tidal Crest" seeks uplifting wordpress site

Looking for a SIMPLE, CLEAN, easy to manage wordpress site for our start-up Branding business. Our company is "Tidal Crest" and the site should reflect our vision.

We formed the company after making the decision never to work the average 9 to 5 work life again. We have vowed to never work in traditional corporate culture again. We are committed to a happier life with reduced stress and increased job satisfaction.

We want to build brands that make people happy.

We want to work with people who believe that you don’t have to be an asshole to be successful.

We believe that success should not be measured in monetary terms, but rather in happiness scores.

We believe in the Corwin Ashdale song lyric "Rivers bend toward evening”.

We love sunflowers.

We prefer brevity over long wind.

We are motivated by creativity not money.

We love spending time with friends and family, and see this as our main priority in life.

We know life is short.

```html
<!DOCTYPE html>
<html lang="en">
<head>
<meta charset="utf-8">
<title>Tidal Crest</title>
<link href="https://fonts.googleapis.com/css2?family=Roboto:ital,wght@0,300;0,400;0,500;1,300&display=swap" rel="stylesheet">
<style>
  :root{
    --pink:#ee1660;
    --pink-dark:#b8153f;
    --orange:#fdb01b;
    --green:#7dc665;
    --teal:#00afc6;
    --ink:#222;
    --body:#3a3a3a;
    --footer:#262626;
    --muted:#bdbdbd;
    --hero-top:#5b6e6a;
    --hero-bottom:#5a6a3a;
    --white:#fff;
  }
  *{margin:0;padding:0;box-sizing:border-box}
  html,body{width:909px;height:1200px;overflow:hidden;background:var(--white)}
  body{font-family:"Roboto",sans-serif;font-weight:300;color:var(--ink);position:relative}

  .hero{position:absolute;left:0;top:0;width:909px;height:447px;overflow:hidden}
  .hero-photo{position:absolute;inset:0;background:linear-gradient(180deg,var(--hero-top) 0%,var(--hero-bottom) 100%)}

  .brand-badge{position:absolute;left:56px;top:18px;width:105px;height:105px;border-radius:50%;
    background:var(--pink);display:flex;align-items:center;justify-content:center}
  .brand-name{color:var(--white);font-weight:500;font-size:19px;letter-spacing:.5px;text-align:center;line-height:1.05}

  .account-links{position:absolute;left:714px;top:65px;font-size:9px;font-weight:400;color:var(--white);letter-spacing:.3px;white-space:nowrap}
  .account-links .signup{color:var(--pink)}
  .menu-toggle{position:absolute;left:826px;top:57px;width:27px;height:27px;border:1.5px solid var(--white)}
  .menu-toggle span{position:absolute;left:5px;width:14px;height:2px;background:var(--white)}

  .hero-title{position:absolute;left:0;width:909px;top:190px;text-align:center;color:var(--white);
    font-size:48px;font-weight:300;letter-spacing:.5px;white-space:nowrap}
  .hero-arrow{position:absolute;top:204px}
  .hero-arrow.prev{left:44px}
  .hero-arrow.next{left:836px}
  .scroll-down{position:absolute;left:425px;top:373px}

  .welcome{position:absolute;top:472px;left:0;width:909px;text-align:center}
  .section-title{font-size:21px;font-weight:300;color:var(--ink)}
  .welcome p{margin:9px auto 0;width:790px;font-size:9.4px;line-height:16px;color:var(--body)}

  .services{position:absolute;left:0;top:590px;width:909px;height:261px}
  .services svg.bands{position:absolute;inset:0}
  .service{position:absolute;top:0;width:200px;text-align:center;color:var(--white)}
  .service .icon{position:absolute;left:70px;top:44px;width:60px;height:60px}
  .service h3{position:absolute;top:128px;width:200px;font-size:19px;font-weight:300}
  .service p{position:absolute;top:158px;left:25px;width:150px;font-size:9.6px;line-height:16px;color:rgba(255,255,255,.85)}

  .testimonials{position:absolute;top:874px;left:0;width:909px;text-align:center}
  .quote{margin:10px auto 0;width:740px;font-size:9.4px;line-height:16px;font-style:italic;color:var(--body)}
  .quote-mark{position:absolute;top:30px;font-size:34px;font-weight:500;color:var(--muted);line-height:1}
  .quote-mark.open{left:56px}
  .quote-mark.close{left:835px}
  .author{margin-top:9px;font-size:9.6px;font-weight:400;color:var(--pink)}
  .dots{margin-top:18px;display:flex;justify-content:center;gap:7px}
  .dots span{width:5px;height:5px;border-radius:50%;background:#aaa}
  .dots span.active{background:#555}

  .site-footer{position:absolute;left:0;top:1050px;width:909px;height:150px;background:var(--footer);text-align:center}
  .footer-badge{position:absolute;left:415px;top:-32px;width:79px;height:79px;border-radius:50%;background:var(--white);
    display:flex;align-items:center;justify-content:center}
  .footer-badge div{width:65px;height:65px;border-radius:50%;background:var(--pink);display:flex;align-items:center;justify-content:center;
    color:var(--white);font-weight:500;font-size:11px;line-height:1.1}
  .copyright{position:absolute;top:63px;width:909px;font-size:9.6px;color:#cfcfcf;font-weight:400}
  .social{position:absolute;top:98px;left:0;width:909px;display:flex;justify-content:center;gap:5px}
  .social span{width:21px;height:21px;border-radius:50%;background:#8a8a8a}
</style>
</head>
<body>

<header class="hero">
  <div class="hero-photo" role="img" aria-label="Hero photograph of a sunflower head against a cloudy sky"></div>

  <div class="brand-badge"><span class="brand-name">Tidal<br>Crest</span></div>

  <nav class="account-links">LOG IN &nbsp;|&nbsp; <span class="signup">SIGN UP</span></nav>
  <div class="menu-toggle" aria-label="Menu">
    <span style="top:6px"></span><span style="top:11px"></span><span style="top:16px"></span>
  </div>

  <h1 class="hero-title">Rivers Bend Toward Evening..</h1>

  <svg class="hero-arrow prev" width="30" height="44" viewBox="0 0 30 44"><polyline points="24,4 6,22 24,40" fill="none" stroke="rgba(255,255,255,.75)" stroke-width="4"/></svg>
  <svg class="hero-arrow next" width="30" height="44" viewBox="0 0 30 44"><polyline points="6,4 24,22 6,40" fill="none" stroke="rgba(255,255,255,.75)" stroke-width="4"/></svg>

  <svg class="scroll-down" width="38" height="38" viewBox="0 0 38 38">
    <circle cx="19" cy="19" r="17.5" fill="var(--pink-dark)" stroke="#fff" stroke-width="1.5"/>
    <polyline points="13,16 19,22 25,16" fill="none" stroke="#fff" stroke-width="1.6"/>
  </svg>
</header>

<section class="welcome">
  <h2 class="section-title">Welcome to Our Website</h2>
  <p>Aliquam molestie, mi et imperdiet euismod, dui purus auctor tellus, et interdum lacus lectus et ante. Sed accumsan sollicitudin sapien, sit amet adipiscing turpis gravida ac. In congue, neque ac lobortis volutpat, libero mauris varius mi, vitae suscipit ipsum ligula vitae risus. Duis aliquam nibh a dui iaculis viverra id a velit. Vivamus egestas risus in magna varius commodo. Sed semper viverra egestas. Etiam pretium porttitor lectus, vel ornare neque porta volutpat.</p>
</section>

<section class="services">
  <svg class="bands" width="909" height="261" viewBox="0 0 909 261">
    <polygon points="0,0 282,0 210,261 0,261" fill="var(--pink)"/>
    <polygon points="282,0 490,0 419,261 210,261" fill="var(--orange)"/>
    <polygon points="490,0 700,0 629,261 419,261" fill="var(--green)"/>
    <polygon points="700,0 909,0 909,261 629,261" fill="var(--teal)"/>
    <g stroke="#fff" stroke-width="1"><line x1="282" y1="0" x2="210" y2="261"/><line x1="490" y1="0" x2="419" y2="261"/><line x1="700" y1="0" x2="629" y2="261"/></g>
  </svg>

  <div class="service" style="left:36px">
    <svg class="icon" viewBox="0 0 60 60" fill="none" stroke="#fff" stroke-width="2.5">
      <circle cx="20" cy="18" r="8"/><circle cx="20" cy="18" r="3"/>
      <circle cx="10" cy="34" r="5"/>
      <rect x="25" y="26" width="28" height="20"/><line x1="22" y1="50" x2="58" y2="50"/>
    </svg>
    <h3>Heading 1</h3><p>Duis aliquam nibh a dui iaculis viverra id a velit.</p>
  </div>

  <div class="service" style="left:242px">
    <svg class="icon" viewBox="0 0 60 60" fill="none" stroke="#fff" stroke-width="2">
      <polyline points="6,4 6,54 56,54"/><polyline points="2,9 6,4 10,9"/><polyline points="51,50 56,54 51,58"/>
      <polyline points="10,44 20,30 28,36 38,22 46,28 54,16"/><polyline points="10,36 20,24 30,32 44,18"/>
    </svg>
    <h3>Heading 1</h3><p>Duis aliquam nibh a dui iaculis viverra id a velit.</p>
  </div>

  <div class="service" style="left:449px">
    <svg class="icon" viewBox="0 0 60 60" fill="#fff">
      <polygon points="6,26 40,10 46,40 12,40"/><polygon points="14,40 22,40 26,54 19,56"/>
      <g stroke="#fff" stroke-width="2.5"><line x1="50" y1="16" x2="56" y2="10"/><line x1="52" y1="24" x2="60" y2="24"/><line x1="46" y1="8" x2="48" y2="2"/></g>
    </svg>
    <h3>Heading 1</h3><p>Duis aliquam nibh a dui iaculis viverra id a velit.</p>
  </div>

  <div class="service" style="left:669px">
    <svg class="icon" viewBox="0 0 60 60" fill="#fff" stroke="#fff" stroke-width="2.5">
      <line x1="18" y1="30" x2="44" y2="14"/><line x1="18" y1="30" x2="44" y2="46"/>
      <circle cx="16" cy="30" r="7"/><circle cx="45" cy="13" r="7"/><circle cx="45" cy="47" r="7"/>
    </svg>
    <h3>Heading 1</h3><p>Duis aliquam nibh a dui iaculis viverra id a velit.</p>
  </div>
</section>

<section class="testimonials">
  <h2 class="section-title">Testimonials</h2>
  <span class="quote-mark open">&ldquo;</span>
  <span class="quote-mark close">&rdquo;</span>
  <p class="quote">Aliquam molestie, mi et imperdiet euismod, dui purus auctor tellus, et interdum lacus lectus et ante. Sed accumsan sollicitudin sapien, sit amet adipiscing turpis gravida ac. In congue, neque ac lobortis volutpat, libero mauris varius mi, vitae suscipit ipsum ligula vitae risus. Duis aliquam nibh a dui iaculis viverra id a velit.</p>
  <p class="author">Name Gose Here</p>
  <div class="dots"><span class="active"></span><span></span><span></span></div>
</section>

<footer class="site-footer">
  <div class="footer-badge"><div>Tidal<br>Crest</div></div>
  <p class="copyright">Copyright© 2015.Company Name.All Right Reserved</p>
  <div class="social"><span></span><span></span><span></span><span></span><span></span></div>
</footer>

</body>
</html>
```